Business Card Design

New business card design

Target Market(s)

Residential & Commercial Property Managers

Industry/Entity Type

Plumbing Services

Contact Information for Business Card

Name - Rowan Keddle, title - Director, Phone Number - 0431 286 517, email - rowan@tbk-plumbing.com.au, Company ABN - 73 215 904 386,

Font styles to use
Sans Serif

Colors
0054AA
0677BA
7BADD7
CADEEF
E8F1F8

```html
<!DOCTYPE html>
<html lang="en">
<head>
<meta charset="utf-8">
<title>TBK Plumbing Services – Business Card</title>
<link rel="stylesheet" href="https://fonts.googleapis.com/css2?family=Michroma&family=Roboto:wght@300;400&display=swap">
<style>
  :root {
    --stage: #2b2c2e;
    --card: #1e2328;
    --card-edge: #252b31;
    --ink: #ffffff;
    --accent: #1aa3e8;
    --pattern-light: #2a343d;
    --pattern-dark: #1a1f24;
  }
  * { box-sizing: border-box; margin: 0; padding: 0; }
  html, body {
    width: 1200px; height: 1108px; overflow: hidden;
    background: var(--stage);
  }
  .canvas {
    position: relative; width: 1200px; height: 1108px;
    display: flex; justify-content: center; align-items: center; gap: 60px;
  }
  .card {
    position: relative; width: 420px; height: 690px;
    background: var(--card);
    border-radius: 24px;
    box-shadow: 0 18px 40px rgba(0,0,0,.45);
    overflow: hidden;
    font-family: "Roboto", sans-serif;
    color: var(--ink);
  }
  /* Front */
  .brand {
    position: absolute; top: 120px; left: 0; right: 0;
    text-align: center;
  }
  .brand-name {
    font-family: "Roboto", sans-serif; font-weight: 300;
    font-size: 124px; line-height: 1; letter-spacing: 4px;
    display: inline-flex; align-items: center; gap: 12px;
  }
  .brand-dot {
    display: inline-block; width: 22px; height: 22px; border-radius: 50%;
    background: var(--accent); margin-top: 60px;
  }
  .brand-tagline {
    margin-top: 18px;
    font-weight: 300; font-size: 13px; letter-spacing: 10px;
    text-transform: lowercase;
  }
  .contact {
    position: absolute; top: 420px; left: 0; right: 0; text-align: center;
  }
  .contact-name {
    font-family: "Michroma", sans-serif; font-size: 22px; letter-spacing: 1px;
    text-transform: uppercase;
  }
  .contact-role { color: var(--accent); font-size: 21px; margin-top: 6px; }
  .divider {
    width: 40px; height: 2px; background: var(--accent);
    margin: 14px auto;
  }
  .contact-line { font-size: 19px; line-height: 1.45; }
  /* Back */
  .back-pattern {
    position: absolute; inset: 0;
    background: linear-gradient(135deg, var(--pattern-light) 0%, var(--pattern-dark) 60%, var(--pattern-light) 100%);
  }
  .back-brand {
    position: absolute; right: 50px; bottom: 230px;
  }
  .back-brand .brand-name { font-size: 64px; gap: 8px; }
  .back-brand .brand-dot { width: 12px; height: 12px; margin-top: 30px; }
</style>
</head>
<body>
<main class="canvas">
  <section class="card card-front" aria-label="Business card front">
    <div class="brand">
      <div class="brand-name">tbk<span class="brand-dot"></span></div>
      <div class="brand-tagline">plumbing services</div>
    </div>
    <div class="contact">
      <div class="contact-name">Rowan Keddle</div>
      <div class="contact-role">Director</div>
      <div class="divider"></div>
      <div class="contact-line">0431 286 517</div>
      <div class="contact-line">rowan@tbk-plumbing.com.au</div>
      <div class="divider"></div>
      <div class="contact-line">Company ABN - 73 215 904 386</div>
    </div>
  </section>

  <section class="card card-back" aria-label="Business card back">
    <div class="back-pattern" role="img" aria-label="Faint repeating brand-name pattern across the card"></div>
    <div class="back-brand">
      <div class="brand-name">tbk<span class="brand-dot"></span></div>
    </div>
  </section>
</main>
</body>
</html>
```